Whitcombe Business Card Design

The name of the business is Dario Whitcombe, CPA LLC
The service that we offer is Accounting, Tax & Consulting Services. I need it to have the following items:
Dario Whitcombe, Principal
Phone Number
Email Address
Physical Address

I have attached the company logo, one in black and one in white. Please provide a design in black background and the other in white background. Please include "Accounting, Tax & Consulting Services". I want the business card to be clean and very professional.

```html
<!DOCTYPE html>
<html lang="en">
<head>
<meta charset="utf-8">
<title>Dario Whitcombe, CPA LLC — Business Cards</title>
<link href="https://fonts.googleapis.com/css2?family=Montserrat:wght@400;500;600;700;800&display=swap" rel="stylesheet">
<style>
  :root {
    --bg: #1a1a1a;
    --card-black: #1d1d1e;
    --card-white: #ffffff;
    --brand-red: #9b1c1f;
    --ink-dark: #2b2b2d;
    --ink-grey: #8a8a8c;
    --ink-light: #f2f2f2;
  }
  * { box-sizing: border-box; margin: 0; padding: 0; }
  html, body {
    width: 1200px; height: 988px; overflow: hidden;
    background: var(--bg);
    font-family: "Montserrat", sans-serif;
  }
  .sheet {
    position: relative; width: 1200px; height: 988px;
  }
  .card {
    position: absolute; left: 250px;
    width: 700px; height: 400px;
    overflow: hidden;
    box-shadow: 0 10px 30px rgba(0,0,0,.5);
  }
  .card--front { top: 64px; background: var(--card-black); }
  .card--back { top: 524px; background: var(--card-black); display: flex; }

  /* Front */
  .front-brand {
    position: absolute; left: 110px; top: 138px;
  }
  .wordmark {
    display: flex; align-items: center; gap: 14px;
  }
  .wordmark__square {
    width: 34px; height: 34px; background: var(--brand-red);
  }
  .wordmark__name {
    font-weight: 600; letter-spacing: .04em; text-transform: uppercase;
  }
  .front-brand .wordmark__name { font-size: 27px; color: var(--ink-grey); }
  .front-brand .credential {
    margin-top: 10px; margin-left: 48px;
    font-size: 19px; font-weight: 600; letter-spacing: .16em;
    color: var(--ink-grey); text-transform: uppercase;
  }
  .front-brand .services {
    margin-top: 18px; margin-left: 48px;
    font-size: 17px; font-weight: 700; color: var(--ink-grey);
  }

  /* Back */
  .back-brand {
    width: 46%; background: var(--card-white);
    display: flex; flex-direction: column; align-items: center; justify-content: center;
  }
  .back-brand .wordmark { gap: 9px; }
  .back-brand .wordmark__square { width: 18px; height: 18px; }
  .back-brand .wordmark__name { font-size: 16px; color: var(--ink-dark); }
  .back-brand .credential {
    margin-top: 6px; font-size: 10.5px; font-weight: 500; letter-spacing: .2em;
    color: var(--ink-grey); text-transform: uppercase;
  }
  .back-info { position: relative; flex: 1; }
  .name-band {
    position: absolute; top: 78px; left: 0; right: -2px; height: 52px;
    background: var(--brand-red);
    display: flex; align-items: center; padding-left: 30px;
    color: var(--ink-light); font-size: 20px; font-weight: 800; text-transform: uppercase;
  }
  .contact-list {
    position: absolute; top: 160px; left: 26px; right: 20px;
    list-style: none;
  }
  .contact-item {
    display: flex; align-items: center; gap: 14px;
    color: var(--ink-light); font-size: 14.5px; line-height: 1.4;
    margin-bottom: 14px;
  }
  .contact-icon {
    flex: none; width: 26px; height: 26px; border-radius: 50%;
    background: var(--brand-red);
    display: flex; align-items: center; justify-content: center;
  }
  .contact-icon svg { width: 14px; height: 14px; fill: var(--ink-light); }
</style>
</head>
<body>
<main class="sheet">

  <section class="card card--front" aria-label="Business card front">
    <div class="front-brand">
      <div class="wordmark">
        <span class="wordmark__square"></span>
        <span class="wordmark__name">Dario Whitcombe, CPA LLC</span>
      </div>
      <p class="credential">Certified Public Accountant</p>
      <p class="services">Accounting, Tax &amp; Consulting Services</p>
    </div>
  </section>

  <section class="card card--back" aria-label="Business card back">
    <div class="back-brand">
      <div class="wordmark">
        <span class="wordmark__square"></span>
        <span class="wordmark__name">Dario Whitcombe, CPA LLC</span>
      </div>
      <p class="credential">Certified Public Accountant</p>
    </div>

    <div class="back-info">
      <h1 class="name-band">Dario Whitcombe, Principal</h1>
      <ul class="contact-list">
        <li class="contact-item">
          <span class="contact-icon">
            <svg viewBox="0 0 24 24"><path d="M12 2a7 7 0 0 0-7 7c0 5 7 13 7 13s7-8 7-13a7 7 0 0 0-7-7zm0 9.5A2.5 2.5 0 1 1 12 6.5a2.5 2.5 0 0 1 0 5z"/></svg>
          </span>
          <span>#208-C, Harrow Point Plaza,<br>Linden Road, Fairhaven, 420718</span>
        </li>
        <li class="contact-item">
          <span class="contact-icon">
            <svg viewBox="0 0 24 24"><path d="M6.6 10.8a15 15 0 0 0 6.6 6.6l2.2-2.2a1 1 0 0 1 1-.25 11.4 11.4 0 0 0 3.6.6 1 1 0 0 1 1 1V20a1 1 0 0 1-1 1A17 17 0 0 1 3 4a1 1 0 0 1 1-1h3.5a1 1 0 0 1 1 1c0 1.25.2 2.45.6 3.6a1 1 0 0 1-.25 1z"/></svg>
          </span>
          <span>555-214-7390</span>
        </li>
        <li class="contact-item">
          <span class="contact-icon">
            <svg viewBox="0 0 24 24"><path d="M3 5h18v14H3zm2 2v.5l7 4.5 7-4.5V7zm0 2.9V17h14V9.9l-7 4.5z"/></svg>
          </span>
          <span>info@dariowhitcombecpa.com</span>
        </li>
        <li class="contact-item">
          <span class="contact-icon">
            <svg viewBox="0 0 24 24"><path d="M12 2a10 10 0 1 0 0 20 10 10 0 0 0 0-20zm6.9 6h-3a15 15 0 0 0-1.3-3.9A8 8 0 0 1 18.9 8zM12 4c.8 1.2 1.5 2.5 1.9 4h-3.8c.4-1.5 1.1-2.8 1.9-4zM4.3 14a8 8 0 0 1 0-4h3.4a16 16 0 0 0 0 4zm.8 2h3a15 15 0 0 0 1.3 3.9A8 8 0 0 1 5.1 16zm3-8h-3a8 8 0 0 1 4.3-3.9A15 15 0 0 0 8.1 8zM12 20c-.8-1.2-1.5-2.5-1.9-4h3.8c-.4 1.5-1.1 2.8-1.9 4zm2.3-6H9.7a14 14 0 0 1 0-4h4.6a14 14 0 0 1 0 4zm.3 5.9a15 15 0 0 0 1.3-3.9h3a8 8 0 0 1-4.3 3.9zM16.3 14a16 16 0 0 0 0-4h3.4a8 8 0 0 1 0 4z"/></svg>
          </span>
          <span>www.dariowhitcombecpa.com</span>
        </li>
      </ul>
    </div>
  </section>

</main>
</body>
</html>
```